Business Card Design - Amberfield Court

We are looking at a new design for our business cards that has a modern and professional look. We run a residential aged care facility focussing on the care of residents. The cards will be used for potential clients, consultants and business opportunities in this sector. Blue and white is our main colours and would to see these colours incorporated in the design.
Industry/Entity Type
Business
Contact Information for Business Card
Amberfield Court, Darren Walsh, dwalsh@amberfieldcourt.com.au, Finance Manager, 0472 639 208, BCom, 37 Marrabel Crescent, Brindle Vale, Qld 4093.
Look and feel
Each slider illustrates characteristics of the customer's brand and the style your logo design should communicate.

```html
<!DOCTYPE html>
<html lang="en">
<head>
<meta charset="utf-8">
<title>Amberfield Court – Business Card</title>
<link rel="stylesheet" href="https://fonts.googleapis.com/css2?family=Source+Sans+3:ital,wght@0,400;0,600;1,400&display=swap">
<style>
  :root {
    --page-bg: #e4e5e6;
    --card-white: #f3f4f6;
    --brand-blue: #3f6a85;
    --text-dark: #4b4e52;
    --text-grey: #8c8c8c;
    --rule-grey: #b9bcc0;
    --white: #ffffff;
  }
  * { margin: 0; padding: 0; box-sizing: border-box; }
  html, body {
    width: 1105px; height: 1200px; overflow: hidden;
    background: var(--page-bg);
    font-family: "Source Sans 3", Arial, sans-serif;
  }
  .canvas { position: relative; width: 1105px; height: 1200px; }
  .card {
    position: absolute; left: 180px; width: 746px; height: 425px;
  }
  .card--front { top: 119px; background: var(--card-white); }
  .card--back { top: 637px; background: var(--brand-blue); }

  .brand {
    position: absolute; left: 0; right: 0; top: 118px;
    display: flex; justify-content: center; align-items: center; gap: 14px;
  }
  .brand__dot { width: 22px; height: 22px; border-radius: 50%; background: var(--brand-blue); }
  .brand__name {
    font-size: 40px; font-weight: 600; letter-spacing: 1px; color: var(--brand-blue);
  }

  .person {
    position: absolute; right: 406px; top: 248px; text-align: right;
  }
  .person__name { font-size: 27px; font-weight: 600; color: var(--brand-blue); line-height: 1.2; }
  .person__cred { font-size: 21px; }
  .person__title { font-size: 20px; color: var(--text-grey); line-height: 1.45; }
  .person__email { font-size: 19px; font-style: italic; color: var(--text-dark); line-height: 1.45; }

  .divider {
    position: absolute; left: 366px; top: 257px; width: 1px; height: 110px; background: var(--rule-grey);
  }

  .contact {
    position: absolute; left: 386px; top: 252px;
    font-size: 19px; color: var(--text-dark); line-height: 29px;
  }
  .contact__row { display: flex; align-items: center; gap: 8px; }
  .contact__icon { width: 16px; height: 16px; fill: var(--brand-blue); }

  .back-brand {
    position: absolute; left: 0; right: 0; top: 150px;
    display: flex; justify-content: center; align-items: center; gap: 16px;
  }
  .back-brand__dot { width: 26px; height: 26px; border-radius: 50%; background: var(--white); }
  .back-brand__name { font-size: 48px; font-weight: 600; letter-spacing: 1px; color: var(--white); }
  .back-web {
    position: absolute; left: 0; right: 0; top: 284px; text-align: center;
    font-size: 22px; font-style: italic; letter-spacing: 1.5px; color: var(--white);
  }
</style>
</head>
<body>
<main class="canvas">
  <section class="card card--front">
    <div class="brand">
      <span class="brand__dot"></span>
      <span class="brand__name">AMBERFIELD COURT</span>
    </div>

    <div class="person">
      <p class="person__name">Darren Walsh <span class="person__cred">BCom</span></p>
      <p class="person__title">Finance Manager</p>
      <p class="person__email">dwalsh@amberfieldcourt.com.au</p>
    </div>

    <div class="divider"></div>

    <div class="contact">
      <p>37 Marrabel Crescent</p>
      <p>Brindle Vale, Qld 4093.</p>
      <p class="contact__row">
        <svg class="contact__icon" viewBox="0 0 16 16" aria-hidden="true"><path d="M3.6 1.2l2.2 2.6-1.3 1.8c.9 2 2.4 3.5 4.1 4.3l1.8-1.3 2.6 2.2-1.3 2.2C7.2 13.4 2.6 8.8 1.4 2.5z"/></svg>
        <span>0472 639 208</span>
      </p>
      <p class="contact__row">
        <svg class="contact__icon" viewBox="0 0 16 16" aria-hidden="true"><circle cx="8" cy="8" r="7"/><path d="M4 5c2 0 2 2 4 2s1 3-1 4-1 3-2 3M10 2c-1 1 0 2 2 2s2 2 1 3" stroke="#f3f4f6" stroke-width="1.2" fill="none"/></svg>
        <span>www.amberfieldcourt.com.au</span>
      </p>
    </div>
  </section>

  <section class="card card--back">
    <div class="back-brand">
      <span class="back-brand__dot"></span>
      <span class="back-brand__name">AMBERFIELD COURT</span>
    </div>
    <p class="back-web">www.amberfieldcourt.com.au</p>
  </section>
</main>
</body>
</html>
```